Business Cards for new orthopaedic surgery practice

My husband and I are starting our own orthopaedic surgery practice. We are looking for a business card that is uniform, but one will have my name/title and the other will have his. You can just create one design with my name on it for now. But when I choose your design as the winning design I will ask that you add another copy with his name/title.

We are looking for classy, simple, elite all in one. We like dark blues/a little gold/yellow. Something that goes with our logo. We want our logo incorporated. Here is all the info you need:
Business name: RV Bone & Vitality Center
Location: 38517 North Willowmere Ave
Palm Hollow, FL 33990
Phone: 954-218-4063
Fax: 954-582-7341
Email: info@myrvbonecare.example

Names: Lydia Vance, M.D.
Board Certified Hand and Upper Extremity Surgeon

Ebo Dansu, M.D.
Board Certified Hip & Knee Replacement/General Orthopaedic Surgeon

Can decide what you want to put on the back. Maybe a slogan:
Rooted in Care. Focused on You

I am just going to upload our logo. The only thing is if we select you as the winning design, the location, and phone numbers may change. We will need your help to update that once fully solidified.

Industry/Entity Type

Medical

Contact Information for Business Card

Colors
0054AA
0677BA
7BADD7
CADEEF
E8F1F8
0094D4
00A9DD
6FCCEA
C7EBF8
E9F6FB

Requirements
Must have
• class, appeal,
Should not have
• We want to air on the side of masculine if we are looking at masculine vs. feminine feel. But we still want it classy, sophisticated, and something we will love

```html
<!DOCTYPE html>
<html lang="en">
<head>
<meta charset="utf-8">
<title>RV Bone &amp; Vitality Center – Business Card</title>
<link href="https://fonts.googleapis.com/css2?family=Montserrat:wght@400;500;700&display=swap" rel="stylesheet">
<style>
  :root {
    --stage: #222222;
    --navy: #1b2a50;
    --navy-faint: #24365f;
    --gold: #c9a45c;
    --ink: #1a1a1a;
    --paper: #ffffff;
  }
  * { box-sizing: border-box; margin: 0; padding: 0; }
  html, body { width: 1200px; height: 711px; overflow: hidden; }
  body {
    background: var(--stage);
    font-family: "Montserrat", Arial, sans-serif;
    position: relative;
  }
  .card {
    position: absolute;
    top: 201px;
    width: 540px;
    height: 309px;
    border-radius: 22px;
    border: 3px solid var(--gold);
    overflow: hidden;
  }
  .card--back { left: 30px; background: var(--navy); }
  .card--front { left: 630px; background: var(--paper); }

  /* back */
  .back-emblem {
    position: absolute;
    left: 50%; top: 50%;
    width: 230px; height: 230px;
    margin: -115px 0 0 -115px;
    border: 3px solid var(--navy-faint);
    border-radius: 50%;
    display: flex; align-items: center; justify-content: center;
  }
  .back-emblem__name {
    font-weight: 700;
    font-size: 22px;
    line-height: 1.25;
    text-align: center;
    color: var(--navy-faint);
  }

  /* front */
  .accent-bar {
    position: absolute;
    left: 16px; top: 62px;
    width: 9px; height: 58px;
    background: var(--navy);
  }
  .identity { position: absolute; left: 38px; top: 56px; }
  .identity__name {
    font-weight: 700;
    font-size: 21px;
    color: var(--navy);
    letter-spacing: 0.2px;
  }
  .identity__cred { color: var(--gold); }
  .identity__title {
    margin-top: 4px;
    font-size: 11.5px;
    line-height: 1.3;
    color: var(--ink);
  }
  .address {
    position: absolute;
    left: 130px; top: 190px;
    font-size: 11px;
    font-style: normal;
    line-height: 1.35;
    color: var(--ink);
  }
  .contact {
    position: absolute;
    left: 130px; top: 232px;
    list-style: none;
    font-size: 11px;
    line-height: 1.5;
    color: var(--ink);
  }
  .contact li { display: flex; align-items: center; gap: 6px; }
  .contact svg { width: 11px; height: 11px; fill: var(--gold); flex: none; }

  .emblem {
    position: absolute;
    left: 306px; top: 38px;
    width: 214px; height: 214px;
    border: 3px solid var(--gold);
    border-radius: 50%;
    display: flex; align-items: center; justify-content: center;
  }
  .emblem__name {
    font-weight: 700;
    font-size: 21px;
    line-height: 1.25;
    text-align: center;
    color: var(--navy);
  }
</style>
</head>
<body>

<section class="card card--back" aria-label="Card back">
  <div class="back-emblem">
    <p class="back-emblem__name">RV Bone &amp;<br>Vitality<br>Center</p>
  </div>
</section>

<section class="card card--front" aria-label="Card front">
  <div class="accent-bar"></div>
  <div class="identity">
    <h1 class="identity__name">Lydia Vance, <span class="identity__cred">M.D.</span></h1>
    <p class="identity__title">Board Certified Hand and<br>Upper Extremity Surgeon</p>
  </div>

  <address class="address">
    38517 North Willowmere Ave<br>Palm Hollow, FL 33990
  </address>

  <ul class="contact">
    <li>
      <svg viewBox="0 0 24 24" aria-hidden="true"><path d="M3 9c0-3 4-5 9-5s9 2 9 5v2h-5V9c-1-.6-2.5-1-4-1s-3 .4-4 1v2H3zM6 12h12l2 8H4z"/></svg>
      954-218-4063
    </li>
    <li>
      <svg viewBox="0 0 24 24" aria-hidden="true"><path d="M6 2h12v6H6zM3 9h18v9h-3v4H6v-4H3zm5 6v5h8v-5z"/></svg>
      954-582-7341
    </li>
    <li>
      <svg viewBox="0 0 24 24" aria-hidden="true"><path d="M2 5h20v14H2zm2 2v.5l8 5 8-5V7z"/></svg>
      info@myrvbonecare.example
    </li>
  </ul>

  <div class="emblem">
    <p class="emblem__name">RV Bone &amp;<br>Vitality<br>Center</p>
  </div>
</section>

</body>
</html>
```